Brochure for a civil enineering company in A4 format

I need a brochure design for our company TIRO Engineering S.r.l.. We are an engineering consultant company. Our main clients are from the infrastructure industry (geotechnical and underground sectors mainly).
We are looking for a 2 pages (4 faces) fold out design with a glued pocket where we can put individual data sheets.
I need A4 format pages.

Target Market(s)

We are an engineering consultant company. Our main clients are from the infrastructure industry (geotechnical and underground sectors mainly).

Industry/Entity Type

Civil Engineer

Font styles to use
Sans Serif

Requirements
Must have
• Overall: 2 pages in A4 format
Essential style. Bright and modern appearance.
Glued pocket
Logo integrated in a picture on the pocket where I would like to insert a slogan (… tiro engineering … reliable solutions …)
Attached are selected images which the designer can use and edit at their own discretion.
Some advice in the following (anyway designers are free to provide their solutions):
Outer sheets:
Front page with name, logo. It could be nice to have the “m” of the logo integrated in a pictures, also a modified picture (I mean modify one of the attached pictures) so to create a general image and do not tie the cover to a specific job.
Back page: offices address and contact email address. Nice to have one space for a slogan.
Inner sheet: text that I upload in the file “inside-sheets”, possibly with pictures on each sheet. In the right faces insert the glued pocket. On this pages insert the section OUR EXPERIENCE ….with a space for a picture of our team.
Nice to have
• Clean and essential design.
Pictures choosing from the atteched ones. Pictures could be modified in a very light manner to make them a general idea of the work ( I mean geotechnical world) without to be immediately linked to a specific site.
Should not have
• excessive frills

```html
<!DOCTYPE html>
<html lang="it">
<head>
<meta charset="utf-8">
<title>TIRO Engineering – Inner spread</title>
<link href="https://fonts.googleapis.com/css2?family=Open+Sans:ital,wght@0,400;0,600;0,700;0,800;1,700&display=swap" rel="stylesheet">
<style>
  :root{
    --bg:#d9d6dc;
    --paper:#ffffff;
    --brown:#3b2a20;
    --beige:#d8d1bd;
    --ink:#2a2320;
    --blue-dark:#0f3f9c;
    --blue-light:#3f74c4;
    --sky:#2f6fc8;
  }
  *{box-sizing:border-box;margin:0;padding:0}
  html,body{width:1200px;height:675px;overflow:hidden;background:var(--bg);font-family:"Open Sans",sans-serif;color:var(--ink)}
  .spread{position:absolute;left:48px;top:77px;width:1104px;height:520px;display:flex;box-shadow:0 6px 18px rgba(0,0,0,.18)}
  .page{position:relative;width:368px;height:520px;background:var(--paper);overflow:hidden}
  .page + .page{border-left:1px solid #e4e1e6}
  .photo{position:absolute}
  .text{font-size:6.4px;line-height:1.38}
  .text p{margin-bottom:6px}

  /* company page */
  .company .hero{left:0;top:0;width:368px;height:240px;background:linear-gradient(180deg,#2c6fd0 0%,#5b93da 45%,#8a4a3e 70%,#4a4a52 100%)}
  .company .title-band{position:absolute;left:0;top:205px;width:235px;height:50px;background:var(--brown);display:flex;align-items:center;padding-left:18px}
  .company .title-band h2{color:#fff;font-weight:800;font-size:25px;letter-spacing:.5px}
  .company .rule{position:absolute;left:16px;top:268px;width:80px;height:2px;background:var(--ink)}
  .company .text{position:absolute;left:16px;top:276px;width:150px}
  .company .aerial{left:172px;top:262px;width:196px;height:138px;background:linear-gradient(135deg,#7c7a76,#a09d98 50%,#5d7a4a)}
  .company .tunnel-a{left:172px;top:406px;width:96px;height:114px;background:radial-gradient(ellipse at 50% 55%,#1e1f24 10%,#6b6a6e 45%,#a6a3a0 90%)}
  .company .tunnel-b{left:273px;top:406px;width:95px;height:114px;background:radial-gradient(ellipse at 50% 45%,#5b5a5e 10%,#8e8b87 50%,#b7b2aa 90%)}

  /* expertise page */
  .expertise .hero{left:0;top:0;width:368px;height:200px;background:linear-gradient(180deg,#9cbbe0 0%,#d6dde3 35%,#b3a58c 65%,#8c7d66 100%)}
  .expertise .panel{position:absolute;left:0;top:200px;width:368px;height:320px;background:var(--beige)}
  .expertise h2{position:absolute;left:16px;top:212px;font-weight:800;font-size:19px;line-height:1.02;color:var(--brown)}
  .expertise .rule{position:absolute;left:16px;top:256px;width:160px;height:2px;background:var(--brown)}
  .expertise .col-left{position:absolute;left:16px;top:264px;width:165px}
  .expertise .lead{font-style:italic;font-weight:700;font-size:6.8px;line-height:1.35;margin-bottom:8px}
  .expertise .col-right{position:absolute;left:192px;top:212px;width:160px}
  .expertise .site{left:190px;top:372px;width:178px;height:148px;background:linear-gradient(135deg,#6c5a4c,#a79b8e 45%,#c46a35 60%,#7a7670)}

  /* pocket page */
  .pocket-page svg{position:absolute;left:0;top:0}
</style>
</head>
<body>
<main class="spread">
  <section class="page company">
    <div class="photo hero" role="img" aria-label="Tunnel boring machine shield lifted by a red crawler crane under a blue sky"></div>
    <div class="title-band"><h2>OUR COMPANY</h2></div>
    <div class="rule"></div>
    <div class="text">
      <p>TIRO Engineering S.r.l. offre servizi di consulenza tecnica, contrattuale e strategica ai principali attori nei settori delle scienze geologiche, dell'ingegneria geotecnica e dell'ingegneria idraulica. Lavoriamo per mitigare il rischio e ridurre l'incertezza, con flessibilità nella ricerca della soluzione ottimale contribuendo ad aumentare la redditività del progetto.</p>
      <p>TIRO Engineering S.r.l. è una società indipendente che nasce nel luglio 2020 dall'associazione di un gruppo di professionisti che hanno messo a fattor comune la reciproca esperienza maturata in oltre trent'anni di attività come progettisti e consulenti nel settore delle grandi opere di ingegneria civile lavorando come Direttori Tecnici di Main Engineering Companies and as Freelancers.</p>
      <p>TIRO Engineering S.r.l. vuole unire l'esperienza dei Fondatori e delle figure chiave con l'entusiasmo di chi intraprende una nuova attività, per dare vita ad una nuova realtà che si pone come obbiettivo principale il design of infrastructures that are safe, sustainable and economic. Each of our projects represents a long term commitment, we believe in providing safe, reliable, sustainable and innovative solutions. This is and will be our distinctive characteristic.</p>
    </div>
    <div class="photo aerial" role="img" aria-label="Aerial view of a tunnel construction site with shed and steel ribs"></div>
    <div class="photo tunnel-a" role="img" aria-label="Tunnel excavation with steel arch supports"></div>
    <div class="photo tunnel-b" role="img" aria-label="Tunnel face with shotcrete lining"></div>
  </section>

  <section class="page expertise">
    <div class="photo hero" role="img" aria-label="Twin tunnel portals in a hillside excavation with a mobile crane"></div>
    <div class="panel"></div>
    <h2>OUR EXPERTISE<br>AND EXPERIENCE</h2>
    <div class="rule"></div>
    <div class="col-left text">
      <p class="lead">La società nasce dall'associazione di un gruppo di professionisti, con indiscusse competenze ed affidabilità, con esperienza maturata in oltre trent'anni di attività come progettisti e consulenti nel settore delle grandi opere di ingegneria civile: geologia, ingegneria geotecnica ed idraulica ed opere sotterranee sono il "core" delle loro competenze ....</p>
      <p><strong>I soci fondatori sono:</strong><br>Luca: Già Direttore Tecnico e Socio di Deltavia Srl, nel periodo di sua permanenza fino al dicembre 2018, ha per essa firmato tutti i progetti nel campo delle opere sotterranee e la maggior parte di quelli di ingegneria geotecnica. Da gennaio 2019 è Direttore Tecnico di Geostra. Può vantare più di 150 gallerie naturali, e numerosi progetti ed assistenze tecniche nel campo delle strutture geotecniche, delle sistemazioni idrogeologiche e dei versanti e delle opere di protezione ambientale. Negli ultimi dieci anni è stato responsabile di attività di assistenza tecnica, per imprese di costruzione, di opere il cui valore supera i 440 Mio EUR e di servizi di progettazione definitiva e/o esecutiva per opere il cui valore supera i 1400 Mio EUR.</p>
    </div>
    <div class="col-right text">
      <p>Chiara: 30 anni di esperienza professionale. Coinvolta in più di 150 gallerie naturali con lunghezza complessiva superiore a 360 km. Numerosi progetti ed attività di assistenza tecnica nel campo delle strutture, delle sistemazioni idrogeologiche e dei versanti e delle opere di protezione ambientale. Negli ultimi dieci anni responsabile di attività di assistenza tecnica in corso d'opera, per imprese di costruzione, di opere il cui valore supera i 440 Mio EUR e di servizi di progettazione definitiva e esecutiva per opere il cui valore supera i 1400 Mio EUR. Ha svolto attività di verifica ai fini della validazione, in Italia ed all'estero, di numerosi progetti il cui valore complessivo supera i 3400 Mio EUR.</p>
    </div>
    <div class="photo site" role="img" aria-label="Aerial view of an urban construction site with tower crane"></div>
  </section>

  <section class="page pocket-page">
    <svg width="368" height="520" viewBox="0 0 368 520" aria-hidden="true">
      <defs>
        <linearGradient id="pocketFill" x1="0" y1="0" x2="1" y2="1">
          <stop offset="0" stop-color="var(--blue-light)" style="stop-color:#3f74c4"/>
          <stop offset="1" stop-color="#0f3f9c"/>
        </linearGradient>
      </defs>
      <path d="M0 520 L0 330 Q0 300 30 296 L210 282 Q240 280 262 262 L368 180 L368 520 Z" fill="url(#pocketFill)"/>
    </svg>
  </section>
</main>
</body>
</html>
```